Tech business card design

We need an amazing business card design for our new business 'Pexla' a marketing tech startup based in Sydney, Australia. We provide an online marketplace for businesses to search and buy advertising media, connect with service providers and learn more about marketing. We wish to communicate 'cool tech', reliability and professionalism and design based around our logo.

Target Market(s)

Business Owners

Contact Information for Business Card

Name
Position
Email Address
Website
Phone Number

Font styles to use
Other font styles liked:
• Avenir & Avenir Next

Colors

Designer to choose colors to be used in the design.

```html
<!DOCTYPE html>
<html lang="en">
<head>
<meta charset="utf-8">
<title>Pexla Business Card</title>
<link rel="stylesheet" href="https://fonts.googleapis.com/css2?family=Nunito+Sans:wght@400;700;900&display=swap">
<style>
  :root {
    --backdrop: #1c1c1e;
    --navy: #1c2456;
    --navy-deep: #18204d;
    --grey: #7c7c80;
    --white: #ffffff;
    --ghost: #5d6490;
    --ink: #1a2150;
  }
  html, body {
    margin: 0;
    padding: 0;
    width: 1200px;
    height: 803px;
    overflow: hidden;
    background: var(--backdrop);
    font-family: "Nunito Sans", Arial, sans-serif;
  }
  .stage {
    position: relative;
    width: 1200px;
    height: 803px;
  }
  .card {
    position: absolute;
    top: 247px;
    width: 540px;
    height: 309px;
    overflow: hidden;
    box-shadow: 0 10px 30px rgba(0,0,0,0.5);
  }
  .card--front { left: 40px; background: var(--white); }
  .card--back { left: 620px; background: var(--navy); }

  .card__waves {
    position: absolute;
    inset: 0;
    width: 540px;
    height: 309px;
  }
  .brand {
    position: absolute;
    margin: 0;
    font-weight: 900;
    color: var(--ink);
    letter-spacing: -1px;
    line-height: 1;
  }
  .brand__tm {
    font-size: 11px;
    font-weight: 700;
    letter-spacing: 0;
    vertical-align: top;
    margin-left: 4px;
  }
  .card--front .brand {
    left: 30px;
    top: 62px;
    font-size: 84px;
  }
  .card--front .brand__tm { position: relative; top: 50px; }

  .holder {
    position: absolute;
    left: 36px;
    top: 215px;
    color: var(--ink);
  }
  .holder__name {
    margin: 0;
    font-size: 17px;
    font-weight: 900;
    letter-spacing: 0.3px;
  }
  .holder__role {
    margin: 2px 0 0;
    font-size: 13px;
    font-weight: 700;
  }

  .contact {
    position: absolute;
    right: 28px;
    top: 92px;
    margin: 0;
    padding: 0;
    list-style: none;
    color: var(--white);
    font-size: 13px;
    text-align: right;
    line-height: 22px;
  }
  .contact__item { display: flex; justify-content: flex-end; align-items: center; gap: 7px; }
  .contact__icon { width: 12px; height: 12px; fill: var(--white); }
  .contact__address { margin-top: 10px; line-height: 18px; }

  .card--back .brand {
    left: 0;
    right: 0;
    top: 100px;
    text-align: center;
    font-size: 128px;
    color: var(--ghost);
  }
  .card--back .brand__tm { font-size: 14px; position: relative; top: 76px; }
</style>
</head>
<body>
<main class="stage">
  <section class="card card--front" aria-label="Business card front">
    <svg class="card__waves" viewBox="0 0 540 309" aria-hidden="true">
      <path fill="var(--grey)" d="M540,44 C410,54 370,108 322,176 C272,244 140,250 0,256 L0,309 L540,309 Z"/>
      <path fill="var(--white)" d="M540,58 C418,68 380,120 334,186 C284,254 150,262 0,268 L0,309 L540,309 Z"/>
      <path fill="var(--navy)" d="M540,66 C424,76 388,128 342,192 C292,262 156,272 0,278 L0,309 L540,309 Z"/>
      <path fill="none" stroke="var(--white)" stroke-width="2" d="M540,84 C440,94 400,148 356,210 C318,262 230,282 100,292"/>
    </svg>

    <h1 class="brand">pexla<span class="brand__tm">TM</span></h1>

    <div class="holder">
      <p class="holder__name">JOHN SMITH</p>
      <p class="holder__role">Position</p>
    </div>

    <ul class="contact">
      <li class="contact__item">012-345-6789
        <svg class="contact__icon" viewBox="0 0 12 12" aria-hidden="true"><path d="M2.5 0.5 L4.5 3 L3.4 4.4 C4 5.8 5.6 7.6 7.4 8.5 L8.8 7.4 L11.5 9.3 L10 11.5 C5.2 11 1 6.5 0.5 2 Z"/></svg>
      </li>
      <li class="contact__item">info@pexla.com
        <svg class="contact__icon" viewBox="0 0 12 12" aria-hidden="true"><path d="M0 2 H12 V10 H0 Z M0.8 2.6 L6 6.8 L11.2 2.6" stroke="var(--navy)" stroke-width="0.9"/></svg>
      </li>
      <li class="contact__item">www.pexla.com
        <svg class="contact__icon" viewBox="0 0 12 12" aria-hidden="true"><circle cx="6" cy="6" r="5.5"/><path d="M0.5 6 H11.5 M6 0.5 V11.5 M6 0.5 C3 3.5 3 8.5 6 11.5 M6 0.5 C9 3.5 9 8.5 6 11.5" stroke="var(--navy)" stroke-width="0.8" fill="none"/></svg>
      </li>
      <li class="contact__address">Street Name, City Name<br>Zipcode:012345</li>
    </ul>
  </section>

  <section class="card card--back" aria-label="Business card back">
    <p class="brand">pexla<span class="brand__tm">TM</span></p>
  </section>
</main>
</body>
</html>
```